Tallowmere Exteriors Door Hanger design, Postcard and presentation folders Design

we are a home improvement company in Portland Oregon, are main service is roofing but we also do gutters, painting and pressure washing. we are a certified roofing contractor for KRV. We have over 20years of experince in the roofing industry we use top quality materials. Our mission is to do quality work and provide the best service.
Updates

This door hangers are going to be share to homeowners where we are currently working at! I will like to have a square maybe 2 inch wide and 1 inch hide (blank) for me to put the address where we are working at. So we want to give a direct message to homeowners who we are and why we are there for. Our services are roofing, gutters, painting, and pressure washing. But 95% of the door hangers should give the message that we are a roofing contractor. We are also certified by KRV which means all of our new roof projects have a 50 year warranty which only 2% of roofing contractor can offer that. We also offer finance, and all quality work. I will like to add photos of our trucks since all of them are wrap which will build them trust.

Target Market(s)

This door hangers should be custom for Homeowners with residential Homes,,, Average customer are between 40 & 65 Years old.

Industry/Entity Type

Roofing

Contact Information for Business Card

Logo, name, phone number, credentials, and services like roofing gutters painting and pressure washing

Font styles to use
Serif
Sans Serif
Decorative

Colors
33b8a4
5c5c5c

Requirements
Must have
• I want tho have a folder design just like this business card sample i uploaded. Teal and charcoal with services ...
Nice to have
• company trucks, job photo, crew photo and credential photos
Should not have
• I dont want it too busy or crowded..

```html
<!DOCTYPE html>
<html lang="en">
<head>
<meta charset="utf-8">
<title>Tallowmere Exteriors – Door Hanger Cards</title>
<link rel="stylesheet" href="https://fonts.googleapis.com/css2?family=Roboto+Condensed:wght@400;700&family=Roboto:wght@700;900&family=Cinzel:wght@600&display=swap">
<style>
  :root {
    --teal: #1d9687;
    --teal-bright: #33b8a4;
    --charcoal: #5c5c5c;
    --charcoal-dark: #444444;
    --white: #ffffff;
    --stage: #e4e4e4;
    --cyan-soft: #aef5ee;
    --badge-red: #d62a2a;
  }
  * { box-sizing: border-box; margin: 0; padding: 0; }
  html, body { width: 1200px; height: 1019px; overflow: hidden; }
  body { background: var(--stage); position: relative; font-family: "Roboto Condensed", "Arial Narrow", sans-serif; }

  .card { position: absolute; width: 750px; height: 375px; background: var(--white); box-shadow: 0 3px 8px rgba(0,0,0,.35); overflow: hidden; }
  .card--front { left: 176px; top: 108px; }
  .card--back { left: 276px; top: 536px; }

  .front-shapes { position: absolute; inset: 0; }
  .abs { position: absolute; }

  .headline { left: 18px; top: 12px; color: var(--white); font-weight: 700; font-size: 17px; line-height: 21px; }
  .truck-thumb { left: 19px; top: 63px; width: 113px; height: 59px; border: 2px solid var(--white);
    background: linear-gradient(135deg, #8aa7a3, #eef3f2 55%, #3b3f40); }
  .call { left: 140px; top: 56px; color: var(--white); font-weight: 700; font-size: 35px; line-height: 36px; }
  .neighborhood { left: 18px; top: 135px; color: var(--white); font-weight: 700; }
  .neighborhood .small { font-size: 13.5px; line-height: 16px; display: block; }
  .neighborhood .big { font-size: 22px; line-height: 24px; display: block; }

  .brand { left: 470px; top: 150px; width: 270px; text-align: center; }
  .brand-name { display: flex; align-items: center; justify-content: center; gap: 8px; color: var(--teal); font-weight: 700; font-size: 27px; letter-spacing: .5px; }
  .brand-square { width: 14px; height: 14px; background: var(--charcoal); }
  .brand-rule { height: 2px; background: var(--charcoal); margin: 7px 34px 6px; }
  .tagline { font-family: "Cinzel", Georgia, serif; font-weight: 600; color: var(--charcoal); font-size: 13px; letter-spacing: 1px; }

  .cert-badge { left: 18px; top: 308px; width: 114px; height: 40px; background: var(--badge-red); }
  .cert-roof { left: 32px; top: 300px; width: 86px; height: 8px; background: #8a8a8a; clip-path: polygon(10% 100%, 50% 0, 90% 100%); }
  .warranty { left: 139px; top: 313px; color: var(--teal); font-weight: 700; font-size: 16px; line-height: 17px; }
  .warranty .big { font-size: 20px; display: block; }
  .round-badge { left: 260px; top: 308px; width: 38px; height: 38px; border-radius: 50%; border: 3px solid #9a9a9a; }
  .accredit-badge { left: 307px; top: 316px; width: 87px; height: 32px; background: #111; border-radius: 3px; }
  .review-badge { left: 402px; top: 316px; width: 66px; height: 32px; border: 1.5px solid #222; border-radius: 6px; }

  .finance { left: 574px; top: 306px; color: var(--charcoal-dark); font-weight: 700; text-align: center; }
  .finance .big { font-size: 21px; line-height: 21px; display: block; }
  .finance .small { font-size: 11.5px; display: block; letter-spacing: .3px; }

  .truck-photo { left: 7px; top: 7px; width: 420px; height: 259px; background: linear-gradient(160deg, #6f7c70 0%, #b5bcbb 35%, #e8eceb 55%, #2b2e2f 100%); }
  .services { left: 434px; top: 7px; width: 308px; }
  .services-title { height: 38px; background: var(--charcoal); color: var(--white); font-family: "Roboto", Arial, sans-serif; font-weight: 700; font-size: 23px; letter-spacing: 2px; text-align: center; line-height: 38px; }
  .service-grid { display: grid; grid-template-columns: repeat(3, 1fr); gap: 4px; margin-top: 4px; }
  .service-photo { height: 80px; }
  .service-label { height: 23px; background: var(--teal); color: var(--white); font-weight: 700; font-size: 10px; text-align: center; line-height: 23px; margin-top: 2px; }
  .ph-roof { background: linear-gradient(160deg, #8b9aa3, #3a3d42); }
  .ph-gutter { background: linear-gradient(160deg, #d8dbdc, #4a5257); }
  .ph-paint { background: linear-gradient(160deg, #c9ccc7, #2c3238); }
  .ph-siding { background: linear-gradient(180deg, #8d9480, #737a68); }
  .ph-wash { background: linear-gradient(160deg, #c8c2b3, #6e6a60); }
  .ph-attic { background: linear-gradient(160deg, #2f5b9a, #18345e); }

  .web-bar { left: 7px; top: 271px; width: 735px; height: 96px; background: var(--charcoal); color: var(--white); font-family: "Roboto", Arial, sans-serif; font-weight: 700; font-size: 35px; text-align: center; line-height: 96px; }
</style>
</head>
<body>

<section class="card card--front">
  <svg class="front-shapes" width="750" height="375" viewBox="0 0 750 375" aria-hidden="true">
    <defs>
      <linearGradient id="address-fill" x1="0" x2="1" y1="0" y2="0">
        <stop offset="0" stop-color="#8ef2e6"/>
        <stop offset=".35" stop-color="#f4fffd"/>
        <stop offset=".7" stop-color="#b6f7ef"/>
        <stop offset="1" stop-color="#e8fffb"/>
      </linearGradient>
    </defs>
    <polygon points="0,0 599,0 323,191 594,375 0,375" fill="var(--teal)"/>
    <path d="M30,191 L307,191 L456,291 L30,291 Q18,291 18,279 L18,203 Q18,191 30,191 Z" fill="url(#address-fill)"/>
    <polygon points="0,301 503,301 557,359 0,359" fill="var(--white)"/>
  </svg>

  <p class="abs headline">PORTLAND’S TOP-RATED ROOFING COMPANY.<br>Let Our Experts Help With Your Next Home Project.</p>
  <div class="abs truck-thumb" role="img" aria-label="Wrapped company truck"></div>
  <p class="abs call">TALK TO US<br>503-555-0148</p>
  <p class="abs neighborhood"><span class="small">WE ARE WORKING IN YOUR NEIGHBORHOOD</span><span class="big">YOU CAN FIND US HERE</span></p>

  <div class="abs brand">
    <div class="brand-name"><span class="brand-square"></span>Tallowmere Exteriors</div>
    <div class="brand-rule"></div>
    <p class="tagline">WHEN QUALITY MATTERS</p>
  </div>

  <div class="abs cert-roof"></div>
  <div class="abs cert-badge" role="img" aria-label="KRV certified contractor badge"></div>
  <p class="abs warranty">WITH 50 YEAR<span class="big">WARRANTY</span></p>
  <div class="abs round-badge" role="img" aria-label="Approved listing badge"></div>
  <div class="abs accredit-badge" role="img" aria-label="Accredited business badge"></div>
  <div class="abs review-badge" role="img" aria-label="Review site badge"></div>

  <p class="abs finance"><span class="big">WE ALSO</span><span class="small">OFFER FINANCE</span></p>
</section>

<section class="card card--back">
  <div class="abs truck-photo" role="img" aria-label="Photo of wrapped company pickup truck with ladder"></div>

  <div class="abs services">
    <h2 class="services-title">SERVICES</h2>
    <div class="service-grid">
      <div><div class="service-photo ph-roof" role="img" aria-label="Roofer installing shingles"></div><p class="service-label">ROOFING</p></div>
      <div><div class="service-photo ph-gutter" role="img" aria-label="Crew member working on gutters"></div><p class="service-label">GUTTERS</p></div>
      <div><div class="service-photo ph-paint" role="img" aria-label="Painter spraying a house wall"></div><p class="service-label">PAINTING</p></div>
      <div><div class="service-photo ph-siding" role="img" aria-label="Green shingle siding"></div><p class="service-label">SIDING</p></div>
      <div><div class="service-photo ph-wash" role="img" aria-label="Pressure washing a driveway"></div><p class="service-label">PRESSURE WASHING</p></div>
      <div><div class="service-photo ph-attic" role="img" aria-label="Roof underlayment for attic ventilation"></div><p class="service-label">ATTIC VENTILATION</p></div>
    </div>
  </div>

  <p class="abs web-bar">www.TallowmereExteriors.com</p>
</section>

</body>
</html>
```